Website to design and sell sundials: www.gnomonvale.com

We have a website that creates a free paper sundial, we want to migrate from this not profit free website to a website where we will continue offering the free paper sundial model but We will also offer a manufactured sundial and sell it.
In order to understand the project, please visit:
http://www.gnomonvale.com/vertical/sundial.html and
http://www.torvel.net/landing/

The website user journey should be redesigned, including the phases that are,
select language
Show product give info
Creation/edit sundial (could be one or more phases)
View created sundial
Buy sundial.

May some of them could be combined or splitted, what It have more sense.

Requirements
Must have
• A description page user journey offering freemium paper sundial and physical sundial to sell.
• A sundial creation page for "free" paper sundial
• A result page for paper sundial
• A sell page for physical

```html
<!DOCTYPE html>
<html lang="en">
<head>
<meta charset="utf-8">
<title>GnomonVale – Sundial location</title>
<link href="https://fonts.googleapis.com/css2?family=Raleway:wght@400;500;600&family=Open+Sans:wght@400;600&display=swap" rel="stylesheet">
<style>
:root{
  --red:#c8150b;
  --red-dark:#a10f06;
  --nav-active:#8e0d05;
  --orange:#f59a10;
  --green:#6aa41a;
  --green-light:#86c02a;
  --text:#333;
  --muted:#6f6f6f;
  --line:#d9d9d9;
  --field:#f6f6f6;
  --footer:#2b2b2b;
  --map-sea:#9ec2f0;
  --map-land:#b9cf98;
}
*{box-sizing:border-box;margin:0;padding:0}
html,body{width:958px;height:1200px;overflow:hidden;background:#fff}
body{position:relative;font-family:"Raleway",sans-serif;color:var(--text)}
.abs{position:absolute}

/* header */
.brand{left:144px;top:24px;display:flex;align-items:center;gap:8px}
.brand-dot{width:22px;height:22px;border-radius:50%;background:var(--orange)}
.brand-name{font-family:"Raleway",sans-serif;font-weight:600;font-size:24px;color:var(--red);letter-spacing:-.3px}
.lang{left:622px;top:44px;width:68px;height:19px;border:1px solid #ddd;font-family:"Open Sans",sans-serif;font-size:9px;display:flex;align-items:center;gap:4px;padding-left:6px;color:#333}
.lang-flag{width:13px;height:9px;background:#2a4f9c}
.social{left:719px;top:38px;display:flex;gap:0}
.social span{width:24px;height:24px;border:1.5px solid #222;border-radius:50%;display:block;margin-right:0}

/* nav */
.nav{left:0;top:74px;width:958px;height:40px;background:linear-gradient(#d01a0e,var(--red-dark))}
.nav a{position:absolute;top:0;height:40px;line-height:40px;color:#fff;text-decoration:none;font-size:12px;font-weight:500;transform:translateX(-50%);white-space:nowrap}
.nav .active{left:145px;width:82px;transform:none;text-align:center;background:var(--nav-active)}
.nav .sep{position:absolute;top:0;width:1px;height:40px;background:rgba(255,255,255,.18)}

.map{left:0;top:114px;width:958px;height:286px;background:linear-gradient(160deg,var(--map-sea) 0%,#a9cbe9 35%,var(--map-land) 55%,var(--map-sea) 100%)}

/* location */
h2{position:absolute;font-weight:400;font-size:22px;color:#333}
.desc{left:165px;font-family:"Open Sans",sans-serif;font-size:9.5px;color:var(--muted)}
.field{border:1px solid #ccc;background:var(--field);font-family:"Open Sans",sans-serif;font-size:10px;color:#999;padding-left:10px;display:flex;align-items:center}
.go{left:538px;top:520px;width:41px;height:31px;background:var(--orange);color:#fff;font-weight:600;font-size:12px;display:flex;align-items:center;justify-content:center}
.label{font-size:10.5px;color:#444}
.hint{font-size:11.5px;color:#555}
.select-caret{position:absolute;right:8px;top:9px}
.rule{left:156px;top:713px;width:658px;height:1px;background:var(--line)}

/* options */
.card{width:176px;height:127px;background:#eee}
.card-photo{width:176px;height:96px}
.card-label{position:absolute;left:12px;top:103px;display:flex;align-items:center;gap:6px;font-size:11.5px;color:#333}
.radio{width:10px;height:10px;border:1px solid #bbb;border-radius:50%;background:#fff;display:inline-block}
.check{width:16px;height:14px;border:1px solid #bbb;background:#f6f6f6}
.opt-label{font-family:"Open Sans",sans-serif;font-size:9.5px;color:#555}
.create{left:162px;top:1018px;width:136px;height:33px;background:linear-gradient(var(--green-light),var(--green));color:#fff;font-size:13px;display:flex;align-items:center;justify-content:center;border:1px solid #5a8f12}

/* footer */
.footer{left:0;top:1096px;width:958px;height:104px;background:var(--footer)}
.footer a{position:absolute;top:28px;color:#fff;text-decoration:none;font-size:10.5px;font-weight:500}
.copy{position:absolute;left:141px;top:51px;font-family:"Open Sans",sans-serif;font-size:8.5px;color:#999}
</style>
</head>
<body>

<header>
  <div class="abs brand"><span class="brand-dot"></span><span class="brand-name">GnomonVale.com</span></div>
  <div class="abs lang"><span class="lang-flag"></span>English
    <svg width="7" height="5" viewBox="0 0 7 5"><path d="M0 0h7L3.5 5z" fill="#666"/></svg></div>
  <div class="abs social" aria-label="Social links"><span></span><span></span><span></span><span></span></div>
</header>

<nav class="abs nav">
  <a class="active" href="#">HOME</a>
  <a href="#" style="left:273px">ABOUT US</a><span class="sep" style="left:322px"></span>
  <a href="#" style="left:367px">PRODUCTS</a><span class="sep" style="left:414px"></span>
  <a href="#" style="left:473px">WHY SUNDIAL</a><span class="sep" style="left:527px"></span>
  <a href="#" style="left:583px">ORDER NOW</a><span class="sep" style="left:635px"></span>
  <a href="#" style="left:678px">GALLERY</a><span class="sep" style="left:718px"></span>
  <a href="#" style="left:763px">CONTACT</a>
</nav>

<div class="abs map" role="img" aria-label="World map for choosing the sundial location"></div>

<section>
  <h2 style="left:166px;top:436px">Sundial location</h2>
  <p class="abs desc" style="top:470px">Select the location where you want to place your paper sundial, mark a line along building wall where you want to put it.</p>
  <p class="abs desc" style="top:489px">Write your address and press Go! (e.g. Picadilly circus, london, UK)</p>
  <div class="abs field" style="left:163px;top:520px;width:376px;height:31px"></div>
  <div class="abs go">GO</div>

  <span class="abs label" style="left:164px;top:567px">Longitude:</span>
  <span class="abs label" style="left:306px;top:567px">Latitude:</span>
  <span class="abs label" style="left:449px;top:567px">Wall declination:</span>
  <div class="abs field" style="left:164px;top:586px;width:130px;height:27px">0</div>
  <div class="abs field" style="left:306px;top:586px;width:130px;height:27px">0</div>
  <div class="abs field" style="left:449px;top:586px;width:129px;height:27px">0</div>

  <span class="abs hint" style="left:162px;top:633px">Now select the face of the building</span>
  <span class="abs label" style="left:160px;top:665px">Face:</span>
  <div class="abs field" style="left:190px;top:658px;width:44px;height:27px;background:#fff;color:#666">A
    <svg class="select-caret" width="9" height="6" viewBox="0 0 9 6"><path d="M1 1l3.5 3.5L8 1" stroke="#666" fill="none" stroke-width="1.2"/></svg></div>
  <div class="abs rule"></div>
</section>

<section>
  <h2 style="left:160px;top:736px">Sundial Options</h2>
  <div class="abs card" style="left:160px;top:775px">
    <div class="card-photo" role="img" aria-label="Paper sundial fixed on a brick wall" style="background:linear-gradient(90deg,#3a5f8a 0 14%,#a86a4e 14% 100%)"></div>
    <div class="card-label"><span class="radio"></span>Wall sundial</div>
  </div>
  <div class="abs card" style="left:356px;top:775px">
    <div class="card-photo" role="img" aria-label="Paper sundial taped to a window" style="background:linear-gradient(90deg,#2a2018 0 22%,#bfae9a 22% 70%,#7d8a94 70%)"></div>
    <div class="card-label"><span class="radio"></span>Window sundial</div>
  </div>

  <span class="abs opt-label" style="left:162px;top:934px">Banner:</span>
  <div class="abs field" style="left:228px;top:931px;width:193px;height:25px;background:#fff;color:#777;font-size:9px">Paper Sundial</div>
  <span class="abs opt-label" style="left:162px;top:962px">Solar Time:</span>
  <span class="abs radio" style="left:228px;top:964px"></span>
  <span class="abs opt-label" style="left:162px;top:989px">Civil Time:</span>
  <span class="abs radio" style="left:228px;top:989px"></span>

  <span class="abs opt-label" style="left:441px;top:933px">Daylight Saving Time:</span>
  <span class="abs check" style="left:551px;top:934px"></span>
  <span class="abs opt-label" style="left:441px;top:960px">Timezone</span>
  <div class="abs field" style="left:551px;top:954px;width:193px;height:22px;background:#fff;color:#666;font-size:8.5px;padding-left:8px">(GMT +199) LOCAL TIME (SOLAR TIME)</div>
  <span class="abs opt-label" style="left:441px;top:988px">Equation of Time</span>
  <span class="abs check" style="left:570px;top:990px"></span>

  <div class="abs create">Create Sundial</div>
</section>

<footer class="abs footer">
  <a href="#" style="left:141px">HOME</a>
  <a href="#" style="left:195px">ABOUT US</a>
  <a href="#" style="left:273px">PRODUCTS</a>
  <a href="#" style="left:353px">WHY SUNDIAL</a>
  <a href="#" style="left:451px">ORDER NOW</a>
  <a href="#" style="left:540px">GALLERY</a>
  <a href="#" style="left:613px">CONTACT</a>
  <p class="copy">© 2016 Company Name&nbsp; All right reserved&nbsp; Term of Use</p>
</footer>

</body>
</html>
```